Professional Single Page Website Design for Tollbrook Advisory

Tollbrook Advisory is a new business consultancy specializing in providing expert services to small businesses, primarily in the brick-and-mortar retail and food service sectors. We offer a range of services including franchise development and launch, due diligence, and construction management.

Currently, we have a basic website set up at www.tollbrookadvisory.example, but we need a professional touch to enhance its design and functionality.

Project Requirements:
- Single Page Design: For now, we need a single page design that effectively showcases who we are, our services, and contact information.
- Future Expansion: The design should be flexible and scalable for future expansion to include additional pages like specific service offerings, about us, and a dedicated contact page.
- Design Aesthetic: We are looking for a modern yet professional design that aligns with our brand identity.
- Logo: We have a logo that we like, which was also sourced from Pixel Bazaar. The logo files are attached to this project brief.

Key Sections to Include:
- Hero Section: An engaging introduction to Tollbrook Advisory with a strong visual impact.
- About Us: A brief overview of who we are and our mission.
- Team: Section for the profiles of the two principals.
- Services: A clear and concise presentation of our services, including franchise development, due diligence, and construction management.
- Contact Information: Easy-to-find contact details, including a form for inquiries.
- Call to Action: Encouraging visitors to get in touch with us for consultations or further information.

Design Considerations:
- Ensure the design is responsive and mobile-friendly.
- Include high-quality images and icons that complement our services and industry.
- We do not need development services, this is only a design project.

```html
<!DOCTYPE html>
<html lang="en">
<head>
<meta charset="utf-8">
<title>Tollbrook Advisory</title>
<link href="https://fonts.googleapis.com/css2?family=Poppins:wght@400;500;600&display=swap" rel="stylesheet">
<style>
:root{
  --ink:#1f2a33;
  --sage:#97c7b0;
  --sage-text:#8cc3aa;
  --soft:#f4f5f5;
  --body:#2f3438;
  --white:#ffffff;
  --ring:#46525b;
}
*{box-sizing:border-box;margin:0;padding:0}
html,body{width:1200px;height:3501px;overflow:hidden}
body{font-family:'Poppins',sans-serif;color:var(--ink);background:var(--white);position:relative}
.accent{color:var(--sage-text)}
.btn{position:absolute;display:flex;align-items:center;justify-content:center;font-size:12.5px;font-weight:500;border-radius:2px}
.btn-dark{background:var(--ink);color:var(--white)}
.btn-sage{background:var(--sage);color:var(--ink)}

/* header */
.site-header{position:absolute;left:0;top:0;width:1200px;height:91px;background:var(--sage)}
.brand-panel{position:absolute;left:0;top:0;width:394px;height:91px;background:var(--ink);clip-path:polygon(0 0,394px 0,355px 91px,0 91px)}
.brand{position:absolute;left:141px;top:26px;display:flex;align-items:center;gap:10px;color:var(--white);font-size:19px;font-weight:500}
.brand-dot{width:40px;height:40px;border-radius:50%;background:var(--sage)}
.nav a{position:absolute;top:26px;font-size:13px;font-weight:500;color:var(--ink);text-decoration:none}

/* hero */
.hero{position:absolute;left:0;top:91px;width:1200px;height:530px;background:var(--soft)}
.hero-photo{position:absolute;left:560px;top:0;width:640px;height:530px;background:linear-gradient(90deg,rgba(244,245,245,1) 0%,#d9dcdf 18%,#b8c3cc 50%,#9a8470 80%,#c7a98b 100%)}
.hero h1{position:absolute;left:141px;top:88px;font-size:47px;font-weight:600;line-height:57px}
.hero .tag{position:absolute;left:141px;top:199px;font-size:18.5px;font-weight:500}
.hero p{position:absolute;left:141px;top:238px;width:478px;font-size:12.6px;line-height:22px;color:var(--body)}

/* about */
.about-visual{position:absolute;left:197px;top:768px;width:276px;height:276px;transform:rotate(45deg);border-radius:70px;background:linear-gradient(135deg,#c9ccce,#a9523f 45%,#3b4246 70%,#d6d8d9)}
.section-title{font-size:35px;font-weight:600}
.about-title{position:absolute;left:580px;top:716px;font-size:34px}
.about-copy{position:absolute;left:580px;top:771px;width:480px;font-size:11.2px;line-height:19px;color:var(--body)}
.about-copy p{margin-bottom:9px}
.about-copy .btn{position:static;width:106px;height:35px;margin-top:8px}

/* services */
.services{position:absolute;left:0;top:1185px;width:1200px;height:819px;background:#f4f4f4}
.services-title{position:absolute;left:0;width:1200px;top:1245px;text-align:center}
.tabs{position:absolute;left:141px;top:1307px;width:918px;height:147px;border-bottom:1px solid #dcdcdc}
.tab{position:absolute;top:0;height:147px;display:flex;flex-direction:column;align-items:center;justify-content:flex-end;padding-bottom:30px;font-size:12.5px;font-weight:500;text-align:center;line-height:16px}
.tab svg{margin-bottom:14px}
.tab.active{background:var(--ink);color:var(--white)}
.svc-title{position:absolute;left:141px;top:1500px;font-size:25px;font-weight:500;color:var(--sage-text)}
.svc-copy{position:absolute;left:141px;top:1538px;width:430px;font-size:11.3px;line-height:19.3px;color:var(--body)}
.svc-copy p{margin-bottom:10px}
.svc-photo{position:absolute;left:670px;top:1496px;width:389px;height:303px;border-radius:3px;background:radial-gradient(circle at 50% 50%,#eceae8,#dcdad8)}
.arrow{position:absolute;width:36px;height:36px;border-radius:50%;display:flex;align-items:center;justify-content:center}
.arrow.prev{left:84px;top:1629px;border:1.5px solid var(--ink);background:var(--white)}
.arrow.next{left:1079px;top:1629px;background:var(--ink)}

/* cta */
.cta{position:absolute;left:141px;top:1875px;width:918px;height:268px;border-radius:3px;background:linear-gradient(180deg,#4f5e63,#3d4a45 60%,#3f4c50);color:var(--white);text-align:center}
.cta h2{margin-top:46px;font-size:34px;font-weight:600}
.cta p{width:700px;margin:10px auto 0;font-size:14px;line-height:24px;color:#e8ecec}

/* team */
.team-title{position:absolute;left:0;width:1200px;top:2219px;text-align:center}
.member-card{position:absolute;top:2329px;height:226px;border:1px solid #e6e6e6;background:var(--white)}
.member-photo{position:absolute;top:2291px;width:120px;height:120px;background:linear-gradient(180deg,#8a8f94,#4c5257)}
.member-name{position:absolute;top:2353px;font-size:22px;font-weight:500;color:var(--sage-text)}
.member-role{position:absolute;top:2383px;font-size:15px;font-weight:500}
.member-bio{position:absolute;top:2425px;width:368px;font-size:11.6px;line-height:20.4px;color:var(--body)}

/* contact */
.map{position:absolute;left:0;top:2704px;width:599px;height:422px;background:linear-gradient(135deg,#eef0f2,#e2e7ea 60%,#dfe6e0)}
.contact{position:absolute;left:599px;top:2704px;width:601px;height:422px;background:var(--sage)}
.contact-title{position:absolute;left:670px;top:2748px;font-size:33px;font-weight:600}
.field{position:absolute;left:670px;width:389px;height:41px;background:rgba(255,255,255,.18);display:flex;align-items:center;padding-left:14px;gap:9px;font-size:11.5px;color:var(--ink)}

/* footer */
.footer{position:absolute;left:0;top:3126px;width:1200px;height:333px;background:var(--ink);color:var(--white)}
.f-head{position:absolute;top:56px;font-size:16px;font-weight:500;color:var(--white)}
.f-item{position:absolute;display:flex;align-items:center;gap:14px;font-size:13.5px;line-height:19px;color:var(--white)}
.ring{width:36px;height:36px;border-radius:50%;border:1px solid var(--ring);display:flex;align-items:center;justify-content:center;flex:none}
.f-brand{position:absolute;left:830px;top:94px;width:250px;display:flex;flex-direction:column;align-items:center;gap:14px;font-size:23px;font-weight:500;color:var(--white)}
.f-brand .mark{width:90px;height:90px;border-radius:50%;background:var(--sage)}
.copyright{position:absolute;left:0;top:3459px;width:1200px;height:42px;background:var(--sage);display:flex;align-items:center;justify-content:center;font-size:14px}
</style>
</head>
<body>

<header class="site-header">
  <div class="brand-panel"></div>
  <div class="brand"><span class="brand-dot"></span>Tollbrook Advisory</div>
  <nav class="nav">
    <a style="left:555px">Home</a>
    <a style="left:645px">About</a>
    <a style="left:736px">Services</a>
    <a style="left:841px">Team</a>
  </nav>
  <div class="btn btn-dark" style="left:927px;top:14px;width:128px;height:41px">Contact Us</div>
</header>

<section class="hero">
  <div class="hero-photo" role="img" aria-label="Consultant smiling while reviewing documents with a client at a desk"></div>
  <h1>Building Success in<br>Southern California</h1>
  <div class="tag"><span class="accent">Expertise at Every Step :</span> From Planning to Execution</div>
  <p>At Tollbrook, we blend innovative strategies with local market expertise to guide your commercial real estate ventures. Whether you're launching a new restaurant, investing in retail spaces, or expanding a franchise, our dedicated team is here to turn your real estate aspirations into tangible success. Dive into a partnership that grows with you.</p>
  <div class="btn btn-dark" style="left:141px;top:374px;width:128px;height:42px">Contact Us</div>
</section>

<div class="about-visual" role="img" aria-label="Modern brick and glass retail storefront"></div>
<h2 class="section-title about-title">About Tollbrook <span class="accent">Advisory</span></h2>
<div class="about-copy">
  <p>Welcome to Tollbrook Advisory, your trusted partner in navigating the complexities of the real estate and small business markets. Founded by industry veterans Adrian Vale and Kevin Lam, we specialize in providing comprehensive services tailored to the unique needs of our clients. Whether you're a franchisee, a new restaurant owner, or a commercial real estate investor, our expertise in due diligence, construction management, and investment property evaluation ensures you make informed, strategic decisions.</p>
  <p>At Tollbrook Advisory, we are committed to your success. Our approach combines meticulous analysis, strategic insights, &amp; personalized service to help you achieve your business goals. We pride ourselves on our ability to deliver results that exceed expectations, fostering long-term relationships built on trust &amp; excellence.</p>
  <p>Discover how Tollbrook Advisory can support your business journey. Partner with us and experience the difference our dedication and expertise can make.</p>
  <div class="btn btn-sage">Contact Us</div>
</div>

<section class="services"></section>
<h2 class="section-title services-title">Tollbrook <span class="accent">Services</span></h2>
<div class="tabs">
  <div class="tab active" style="left:0;width:169px">
    <svg width="64" height="44" viewBox="0 0 64 44" fill="none" stroke="#97c7b0" stroke-width="2"><path d="M4 16h40M6 16l4-10h28l4 10M8 16v24h34V16M16 40V26h10v14M30 24h8v8h-8z"/><path d="M52 6v34M52 10h8M52 22h8M52 34h8"/></svg>
    Franchise Development<br>&amp; Launch</div>
  <div class="tab" style="left:190px;width:170px">
    <svg width="52" height="44" viewBox="0 0 52 44" fill="none" stroke="#97c7b0" stroke-width="2"><circle cx="20" cy="18" r="10"/><circle cx="28" cy="24" r="9"/><path d="M35 31l10 10"/></svg>
    Due Diligence<br>Services</div>
  <div class="tab" style="left:375px;width:172px">
    <svg width="52" height="44" viewBox="0 0 52 44" fill="none" stroke="#97c7b0" stroke-width="2"><circle cx="22" cy="18" r="8"/><circle cx="22" cy="18" r="3"/><path d="M6 40h40M38 8h8M38 18h8M38 28h8"/></svg>
    Building &amp; Construction<br>Management</div>
  <div class="tab" style="left:580px;width:178px">
    <svg width="52" height="48" viewBox="0 0 52 48" fill="none" stroke="#97c7b0" stroke-width="2"><path d="M8 22L26 6l18 16M12 19v16h28V19"/><circle cx="26" cy="25" r="6"/><path d="M4 44h14l10-6"/></svg>
    Investment Property<br>Evaluation</div>
  <div class="tab" style="left:778px;width:160px">
    <svg width="52" height="48" viewBox="0 0 52 48" fill="none" stroke="#97c7b0" stroke-width="2"><circle cx="26" cy="20" r="15"/><path d="M19 26v-6M26 26v-10M33 26v-8M15 42l6-8"/></svg>
    Market Analysis &amp;<br>Feasibility Studies</div>
</div>
<div class="svc-title">Franchise Development &amp; Launch</div>
<div class="svc-copy">
  <p>At Tollbrook Advisory, our Franchise Development &amp; Launch service is designed to transform your successful business into a thriving franchise. We start by thoroughly evaluating your business model to determine its franchisability. Once confirmed, our team handles every aspect of the franchise setup, including legal documentation, branding, marketing strategies, operational guidelines, and franchisee recruitment.</p>
  <p>Our goal is to ensure a seamless and efficient transition from a single successful location to a robust franchise network, empowering your business to scale effectively and achieve exponential growth. Partner with us to turn your business into a nationwide brand.</p>
</div>
<div class="btn btn-sage" style="left:141px;top:1756px;width:106px;height:34px">Contact Us</div>
<div class="svc-photo" role="img" aria-label="Colourful map pins linked by red string forming a network"></div>
<div class="arrow prev"><svg width="16" height="16" viewBox="0 0 16 16" fill="none" stroke="#1f2a33" stroke-width="1.8"><path d="M14 8H2M7 3L2 8l5 5"/></svg></div>
<div class="arrow next"><svg width="16" height="16" viewBox="0 0 16 16" fill="none" stroke="#ffffff" stroke-width="1.8"><path d="M2 8h12M9 3l5 5-5 5"/></svg></div>

<section class="cta" role="img" aria-label="Aerial view of a commercial office park with trees">
  <h2>Unlock Your Business <span class="accent">Potential Today!</span></h2>
  <p>At Tollbrook Advisory, we're dedicated to turning your business aspirations into reality. Our expertise and commitment ensure you make informed, strategic decisions that drive success. Take the first step towards achieving your goals with confidence.</p>
  <div class="btn btn-sage" style="left:393px;top:180px;width:132px;height:31px">Get Started Now</div>
</section>

<h2 class="section-title team-title">Our Leadership <span class="accent">Team</span></h2>
<div class="member-card" style="left:183px;width:402px"></div>
<div class="member-photo" style="left:141px" role="img" aria-label="Portrait of principal Kevin Lam"></div>
<div class="member-name" style="left:284px">Kevin Lam</div>
<div class="member-role" style="left:284px">Principal</div>
<p class="member-bio" style="left:202px">Kevin Lam is a seasoned real estate expert with extensive experience in project and construction management, and a licensed real estate agent in California. Fluent in both English and Korean, he specializes in commercial real estate, bringing invaluable expertise to Tollbrook Advisory...</p>

<div class="member-card" style="left:656px;width:403px"></div>
<div class="member-photo" style="left:614px;background:linear-gradient(180deg,#9fb8cc,#d8dde0 60%,#7c8a93)" role="img" aria-label="Portrait of principal Adrian Vale"></div>
<div class="member-name" style="left:757px">Adrian Vale</div>
<div class="member-role" style="left:757px">Principal</div>
<p class="member-bio" style="left:675px">Adrian Vale brings almost 20 years of rich experience as a real estate investor and a pivotal role at one of southern California's largest real estate management firms, where he led sales and marketing strategies to elevate property value and investor returns. His vast expertise spans...</p>
<div class="btn btn-sage" style="left:548px;top:2584px;width:104px;height:34px">Contact Us</div>

<div class="map" role="img" aria-label="Street map showing the office location"></div>
<section class="contact"></section>
<h2 class="contact-title">Contact <span style="color:var(--white)">Us</span></h2>
<div class="field" style="top:2810px"><svg width="13" height="13" viewBox="0 0 14 14" fill="none" stroke="#1f2a33" stroke-width="1.2"><circle cx="7" cy="4.5" r="3"/><path d="M1.5 13c0-3 2.5-5 5.5-5s5.5 2 5.5 5"/></svg>Your Name*</div>
<div class="field" style="top:2865px"><svg width="13" height="13" viewBox="0 0 14 14" fill="none" stroke="#1f2a33" stroke-width="1.2"><rect x="1" y="3" width="12" height="9"/><path d="M1 3l6 5 6-5"/></svg>Your Email*</div>
<div class="field" style="top:2919px"><svg width="13" height="13" viewBox="0 0 14 14" fill="none" stroke="#1f2a33" stroke-width="1.2"><path d="M3 1l2.5 3-1.5 1.5c1 2 2.5 3.5 4.5 4.5L10 8.5l3 2.5-1.5 2C6 13 1 8 1 2.5z"/></svg>Your Phone*</div>
<div class="field" style="top:2973px"><svg width="13" height="13" viewBox="0 0 14 14" fill="none" stroke="#1f2a33" stroke-width="1.2"><circle cx="7" cy="3" r="2"/><path d="M5 13V7h4v6"/></svg>Additional Information</div>
<div class="btn btn-dark" style="left:670px;top:3028px;width:389px;height:39px">Submit Now</div>

<footer class="footer">
  <div class="f-head" style="left:141px">Contact Details</div>
  <div class="f-item" style="left:141px;top:96px"><span class="ring"><svg width="14" height="16" viewBox="0 0 14 16" fill="#97c7b0"><path d="M7 0C3.5 0 1 2.6 1 6c0 4 6 10 6 10s6-6 6-10c0-3.4-2.5-6-6-6zm0 8.2A2.2 2.2 0 117 3.8a2.2 2.2 0 010 4.4z"/></svg></span><span>410 Meridian Way Suite 200<br>Lakeview, CA 90000, USA</span></div>
  <div class="f-item" style="left:141px;top:164px"><span class="ring"><svg width="14" height="14" viewBox="0 0 14 14" fill="#97c7b0"><path d="M3 1l2.5 3-1.5 1.5c1 2 2.5 3.5 4.5 4.5L10 8.5l3 2.5-1.5 2C6 13 1 8 1 2.5z"/></svg></span><span>Phone<br>555 014 2290</span></div>
  <div class="f-item" style="left:141px;top:232px"><span class="ring"><svg width="15" height="12" viewBox="0 0 15 12" fill="#97c7b0"><path d="M0 0h15v12H0z"/><path d="M0 0l7.5 6L15 0" stroke="#1f2a33" fill="none"/></svg></span><span>Email<br>info@tollbrookadvisory.example</span></div>

  <div class="f-head" style="left:557px">Follow Us</div>
  <div class="f-item" style="left:557px;top:96px"><span class="ring"><svg width="8" height="8"><circle cx="4" cy="4" r="4" fill="#97c7b0"/></svg></span>Community</div>
  <div class="f-item" style="left:557px;top:143px"><span class="ring"><svg width="8" height="8"><circle cx="4" cy="4" r="4" fill="#97c7b0"/></svg></span>Gallery</div>
  <div class="f-item" style="left:557px;top:190px"><span class="ring"><svg width="8" height="8"><circle cx="4" cy="4" r="4" fill="#97c7b0"/></svg></span>Updates</div>
  <div class="f-item" style="left:557px;top:237px"><span class="ring"><svg width="8" height="8"><circle cx="4" cy="4" r="4" fill="#97c7b0"/></svg></span>Videos</div>

  <div class="f-brand"><span class="mark"></span>Tollbrook Advisory</div>
</footer>

<div class="copyright">©2024 Tollbrook Advisory. All Rights Reserved.</div>

</body>
</html>
```